Website for a Psychologist in Private Practice

I need a cool web design for my website: www.drkalvoric.com. I would like it to look professional. Keep all the current content and add: Space for video; radio spots (see Silver Cedar Tunes Logo below for those); Quick Inquiry; Friendora link; 5 star rating on Rivo; a map; reviews from former patients. I am open to suggestions.

Target Market(s)

Those seeking individual and marital counseling.

Industry/Entity Type

Mental Health

Number of Pages Required

1 page

Font styles to use
Sans Serif
Other font styles liked:
• I'm open but no hard to read script

Requirements
Must have
• All the content on my home page with link for video and radio spots. List services and degrees and expertices (pics not necessary).
Nice to have
• A video of me and radio conversations (logo of Silver Cedar Tunes radio attached).
Should not have
• Cartoons, comedy, etc.... I don't need pictures of services (marital, depression, etc...) Just list those.

```html
<!DOCTYPE html>
<html lang="en">
<head>
<meta charset="utf-8">
<title>Dr. Mara L. Kalvoric — Counseling</title>
<link rel="stylesheet" href="https://fonts.googleapis.com/css2?family=Open+Sans:wght@400;600;700&family=Roboto+Condensed:wght@300&family=Roboto:wght@300;400&display=swap">
<style>
:root{
  --gold:#c9af4e;
  --olive:#8b7a2a;
  --olive-text:#93802c;
  --grey-band:#ebebeb;
  --grey-soft:#f2f2f2;
  --text:#666;
  --white:#fff;
}
*{margin:0;padding:0;box-sizing:border-box}
html,body{width:739px;height:1200px;overflow:hidden;background:var(--white)}
body{position:relative;font-family:"Open Sans",sans-serif;color:var(--text)}
.abs{position:absolute}

/* hero */
.hero{left:0;top:0;width:739px;height:331px;background:var(--grey-band)}
.hero-photo{left:0;top:0;width:739px;height:300px;
  background:linear-gradient(100deg,#5fc7a4 0%,#a9dc9a 22%,#eef0a0 48%,#f6e0a0 60%,#f0d8a8 68%,#c6e8a4 84%,#9fdca2 100%)}
.hero-wave{left:0;top:0}
.site-name{left:50px;top:20px;font-family:"Roboto",sans-serif;font-weight:300;font-size:29px;color:var(--gold);white-space:nowrap}
.tagline{left:49px;top:86px;font-family:"Roboto Condensed",sans-serif;font-weight:300;font-size:26px;line-height:35px;color:var(--olive-text)}
.call{left:48px;top:227px;display:flex;align-items:center}
.call-icon{width:45px;height:45px;border:1.5px solid var(--gold);border-radius:50%;display:flex;align-items:center;justify-content:center;margin-right:6px}
.call-label{font-family:"Roboto",sans-serif;font-size:10px;color:#555}
.call-number{font-family:"Roboto",sans-serif;font-weight:400;font-size:19px;color:var(--gold);margin-top:2px}

.nav{left:47px;top:296px;height:35px;font-family:"Roboto",sans-serif;font-size:13px;color:#555}
.nav a{color:inherit;text-decoration:none;display:flex;align-items:center;height:35px;position:absolute;white-space:nowrap}
.nav .active{background:var(--gold);color:var(--white);left:0;width:71px;justify-content:center}

/* welcome */
.portrait-frame{left:47px;top:374px;width:161px;height:170px;border:1px solid var(--gold);padding:3px}
.portrait{width:100%;height:100%;background:radial-gradient(circle at 50% 40%,#e8c99c 0%,#b8a36a 40%,#3c6a3a 75%,#2f5c8a 100%)}
.welcome-title{left:227px;top:366px;font-family:"Roboto",sans-serif;font-weight:400;font-size:26px;color:var(--olive-text);white-space:nowrap}
.welcome-body{left:228px;top:404px;width:462px;font-size:9.6px;line-height:16px;color:#666}
.btn{left:226px;top:510px;width:108px;height:32px;background:var(--gold);color:var(--white);font-family:"Roboto",sans-serif;font-size:14px;display:flex;align-items:center;justify-content:center}

/* expertise */
.expertise{left:0;top:574px;width:739px;height:236px;background:var(--grey-soft)}
.section-title{left:0;top:30px;width:739px;text-align:center;font-family:"Roboto",sans-serif;font-weight:400;font-size:26px;color:var(--olive-text)}
.skill{width:140px;text-align:center;top:72px}
.skill-icon{width:70px;height:70px;border:1px solid var(--olive);border-radius:50%;margin:0 auto 10px;display:flex;align-items:center;justify-content:center}
.skill-name{font-family:"Roboto",sans-serif;font-size:14px;line-height:17px;color:var(--gold)}

/* media */
.col-title{font-family:"Roboto",sans-serif;font-weight:400;font-size:20px;color:var(--olive-text);white-space:nowrap}
.video{left:52px;top:887px;width:193px;height:119px;background:radial-gradient(circle at 50% 45%,#e4c99a 0%,#b59e66 35%,#4e7a3e 70%,#2f5a7e 100%)}
.small-text{font-size:9.5px;line-height:16px;color:#666}
.track{left:279px;top:928px;display:flex;align-items:center}
.track-play{width:15px;height:15px;border-radius:50%;background:var(--gold);display:flex;align-items:center;justify-content:center;margin-right:4px}
.track-artist{font-size:7.5px;color:#999;line-height:9px}
.track-title{font-family:Arial,sans-serif;font-size:8.5px;color:#111;line-height:10px}
.wave{left:279px;top:956px;width:192px;height:34px;
  background:repeating-linear-gradient(90deg,#c9c9c9 0 1px,transparent 1px 3px)}
.wave-time{left:456px;top:970px;background:var(--gold);color:var(--white);font-size:6px;padding:0 2px}
.wave-plays{left:450px;top:992px;font-size:6.5px;color:#999}
.partner-badge{width:46px;height:36px;background:#e9e3c6;border-radius:3px}
.partner-name{font-family:"Roboto",sans-serif;font-size:13px;color:#555;white-space:nowrap}
.donate{display:flex;align-items:center;font-family:"Roboto",sans-serif;font-size:13px;color:var(--gold);letter-spacing:.5px}

/* footer */
.footer{left:0;top:1038px;width:739px;height:162px;background:var(--grey-soft)}
.footer-rule{left:0;top:22px;width:739px;height:3px;background:var(--olive)}
.to-top{left:347px;top:1px;width:45px;height:45px;border-radius:50%;background:var(--olive);display:flex;align-items:center;justify-content:center}
.social-row{left:0;top:53px;width:739px;display:flex;justify-content:center;gap:22px}
.social{display:flex;align-items:center;gap:7px;font-family:"Open Sans",sans-serif;font-size:11.5px;color:var(--olive)}
.social-dot{width:34px;height:34px;border-radius:50%;background:var(--olive)}
.footer-links{top:100px;left:0;width:739px;display:flex;justify-content:center;gap:27px;font-size:11.5px;color:#555}
.footer-links .current{color:var(--gold)}
.copyright{top:127px;left:0;width:739px;text-align:center;font-size:9.6px;color:#666}
.copyright b{color:var(--olive)}
</style>
</head>
<body>

<header class="abs hero">
  <div class="abs hero-photo" role="img" aria-label="Sunlit photograph of a woman with arms spread wide in a bright meadow"></div>
  <svg class="abs hero-wave" width="739" height="331" viewBox="0 0 739 331">
    <path d="M0,240 C150,190 330,215 470,270 C565,302 650,285 739,224 L739,331 L0,331 Z" fill="#ebebeb"/>
    <path d="M0,240 C150,190 330,215 470,270 C565,302 650,285 739,224" fill="none" stroke="#c9af4e" stroke-width="3"/>
  </svg>
  <div class="abs site-name">Dr. Mara L. Kalvoric</div>
  <div class="abs tagline">Your life can be difficult but<br>also possibly life changing.</div>
  <div class="abs call">
    <div class="call-icon">
      <svg width="20" height="20" viewBox="0 0 24 24"><path d="M6.6 10.8c1.4 2.8 3.8 5.1 6.6 6.6l2.2-2.2c.3-.3.7-.4 1-.2 1.1.4 2.3.6 3.6.6.6 0 1 .4 1 1V20c0 .6-.4 1-1 1C10.6 21 3 13.4 3 4c0-.6.4-1 1-1h3.5c.6 0 1 .4 1 1 0 1.3.2 2.5.6 3.6.1.3 0 .7-.2 1z" fill="#c9af4e"/></svg>
    </div>
    <div>
      <div class="call-label">Call us now</div>
      <div class="call-number">(949) 555 0183</div>
    </div>
  </div>
  <nav class="abs nav">
    <a class="active">HOME</a>
    <a style="left:97px">ABOUT</a>
    <a style="left:193px">SESSIONS</a>
    <a style="left:309px">RESOURCES</a>
    <a style="left:442px">BIO</a>
    <a style="left:511px">CONTACT</a>
  </nav>
</header>

<section class="welcome">
  <div class="abs portrait-frame"><div class="portrait" role="img" aria-label="Portrait photograph of the psychologist"></div></div>
  <h1 class="abs welcome-title">WELCOME TO Dr. Mara L. Kalvoric</h1>
  <p class="abs welcome-body">I'm so glad you are here.&nbsp; Choosing to see a professional for issues in your life can be difficult but also possibly life changing.&nbsp; Many postpone seeking help because they believe doing so acknowledges failure on their part.&nbsp; Reallly? We seek the help of experts all the time (contractors, mechanics, chefs, etc...) and what is more important than your life? Consulting with a neutral party to act in your best interest can be time well spent.&nbsp; So if you are willing to take the time to invest in counseling, make sure that it is with someone that is worth your time.</p>
  <div class="abs btn">READ MORE</div>
</section>

<section class="abs expertise">
  <h2 class="abs section-title">OUR EXPERTISE</h2>
  <div class="abs skill" style="left:36px">
    <div class="skill-icon"><svg width="32" height="28" viewBox="0 0 24 21"><path d="M12 21 2 11C-1 8 .5 1 6 1c3 0 4.5 2 6 3.5C13.5 3 15 1 18 1c5.5 0 7 7 4 10z" fill="#8b7a2a"/></svg></div>
    <div class="skill-name">Dating, Marriage</div>
  </div>
  <div class="abs skill" style="left:168px">
    <div class="skill-icon"><svg width="34" height="28" viewBox="0 0 34 28" fill="#8b7a2a"><circle cx="7" cy="4" r="3"/><rect x="4" y="8" width="6" height="10" rx="1"/><rect x="4" y="17" width="2.5" height="10"/><rect x="7.5" y="17" width="2.5" height="10"/><circle cx="17" cy="11" r="2.2"/><rect x="15" y="14" width="4" height="7"/><rect x="15" y="20" width="1.7" height="7"/><rect x="17.3" y="20" width="1.7" height="7"/><circle cx="27" cy="4" r="3"/><path d="M23 8h8l2 11h-12z"/><rect x="24.5" y="18" width="2.2" height="9"/><rect x="27.5" y="18" width="2.2" height="9"/></svg></div>
    <div class="skill-name">Parenting &amp;<br>Professional<br>Relationship</div>
  </div>
  <div class="abs skill" style="left:301px">
    <div class="skill-icon"><svg width="30" height="32" viewBox="0 0 30 32" fill="#8b7a2a"><circle cx="21" cy="5" r="4"/><path d="M17 10c-4 1-8 6-9 10h6l-3 10h4l4-12h-5l4-6c1 2 2 4 5 5l-1-7z"/></svg></div>
    <div class="skill-name">Depression &amp;<br>Anxiety Issues</div>
  </div>
  <div class="abs skill" style="left:432px">
    <div class="skill-icon"><svg width="32" height="34" viewBox="0 0 32 34" fill="none" stroke="#8b7a2a" stroke-width="1.3"><path d="M9 32v-6c-4-3-6-7-6-12C3 7 9 2 16 2s12 5 12 11l3 6-3 1v4c0 2-2 3-4 3h-3v5"/><circle cx="11" cy="10" r="2"/><circle cx="18" cy="9" r="2"/><circle cx="15" cy="16" r="2"/><circle cx="22" cy="15" r="1.6"/><path d="M11 12v6l4-2M18 11l4 4M11 18v4"/></svg></div>
    <div class="skill-name">Personality<br>Disorders</div>
  </div>
  <div class="abs skill" style="left:564px">
    <div class="skill-icon"><svg width="30" height="30" viewBox="0 0 30 30" fill="none" stroke="#8b7a2a" stroke-width="2"><path d="M15 3a12 12 0 1 0 12 12" stroke-dasharray="3 2.5"/><path d="M15 3a12 12 0 0 0-10 18"/><path d="M15 15l5-5"/><circle cx="15" cy="15" r="1.5" fill="#8b7a2a"/><path d="M3 19l2 3 3-2"/></svg></div>
    <div class="skill-name">Life Management</div>
  </div>
</section>

<section class="media">
  <h3 class="abs col-title" style="left:54px;top:849px">Dr. Mara L. Kalvoric</h3>
  <div class="abs video" role="img" aria-label="Video still of the psychologist introducing her practice"></div>

  <h3 class="abs col-title" style="left:280px;top:849px">Radio Conversation</h3>
  <p class="abs small-text" style="left:280px;top:883px;width:200px">Lorem Ipsum is simply dummy text of the printing and typesetting industry.</p>
  <div class="abs track">
    <div class="track-play"><svg width="6" height="7" viewBox="0 0 6 7"><path d="M1 0l5 3.5L1 7z" fill="#fff"/></svg></div>
    <div>
      <div class="track-artist">Dr. Mara L. Kalvoric</div>
      <div class="track-title">Lorem ipsum is simply dummy text ever</div>
    </div>
  </div>
  <div class="abs wave"></div>
  <div class="abs wave-time">7:05</div>
  <div class="abs wave-plays">▶ 297</div>

  <h3 class="abs col-title" style="left:506px;top:849px">Donate to</h3>
  <p class="abs small-text" style="left:506px;top:883px">A portion of all revenue is donated to</p>
  <div class="abs partner-badge" style="left:505px;top:909px"></div>
  <div class="abs partner-name" style="left:601px;top:904px">Harbor Kids Fund</div>
  <div class="abs donate" style="left:601px;top:924px">
    <svg width="20" height="20" viewBox="0 0 20 20" fill="#c9af4e" style="margin-right:6px"><text x="6" y="10" font-size="11" font-family="Arial">$</text><path d="M1 14h5l4 1h5l3-2v3l-5 3H9l-4-1H1z"/></svg>DONATE
  </div>
  <div class="abs partner-badge" style="left:505px;top:966px"></div>
  <div class="abs partner-name" style="left:601px;top:962px">Cedar Hope Homes</div>
  <div class="abs donate" style="left:601px;top:982px">
    <svg width="20" height="20" viewBox="0 0 20 20" fill="#c9af4e" style="margin-right:6px"><text x="6" y="10" font-size="11" font-family="Arial">$</text><path d="M1 14h5l4 1h5l3-2v3l-5 3H9l-4-1H1z"/></svg>DONATE
  </div>
</section>

<footer class="abs footer">
  <div class="abs footer-rule"></div>
  <div class="abs to-top"><svg width="18" height="16" viewBox="0 0 18 16" fill="none" stroke="#fff" stroke-width="2.2"><path d="M2 8l7-6 7 6M2 14l7-6 7 6"/></svg></div>
  <div class="abs social-row">
    <div class="social"><span class="social-dot"></span>Friendora</div>
    <div class="social"><span class="social-dot"></span>Flitter</div>
  </div>
  <nav class="abs footer-links">
    <span class="current">Home</span><span>About</span><span>Sessions</span><span>Resources</span><span>Bio</span><span>Contact</span>
  </nav>
  <div class="abs copyright">© <b>DR.KALVORIC</b> - 2016. All Rights Reserved.</div>
</footer>

</body>
</html>
```